Refresh Brightpath Coursecraft

Need a new design for e-learning development and web app development site: http://brightpathcoursecraft.example. Need pages for everything on menu bar plus a training services and a web app development services pages and a better page for samples http://brightpathcoursecraft.example/samples5/.

***Must be programmed in html 5. NO CMS. No WP. No Plume. Straight html/css.

Target Market(s)

government

Industry/Entity Type

Government

Coding

Coded - Design and coding required

Number of Pages Required

1 page

Requirements
Must have
• Must be coded in html5/css. No CMS.
• Divided so you can easily see that we offer 3 separate services:
• Live Training - E-Learning Development - Web App Development
• A way to display logos of all our clients like on bottom of this page: https://www.quorvatests.example (this is also our website so you can copy all these logos)
• List both our Denver location which is already on our website plus our office in Velmoro Plaza. Street 62 Sur, 14-87. Medellín, Antioquia.
• A page like this for our web app dev services https://www.tekvanu.example/product-development
Should not have
• CMS

```html
<!DOCTYPE html>
<html lang="en">
<head>
<meta charset="utf-8">
<title>Brightpath Coursecraft Solutions</title>
<link href="https://fonts.googleapis.com/css2?family=Open+Sans:wght@300;400;600;700&display=swap" rel="stylesheet">
<style>
:root{
  --hero:#6ca7e2;
  --arc:#1b68b5;
  --orange:#f29b26;
  --ink:#2b2b2b;
  --muted:#5c5c5c;
  --pale:#f3f6fa;
  --dark:#1f1f1f;
  --white:#ffffff;
}
*{box-sizing:border-box;margin:0;padding:0}
html,body{width:1200px;height:4489px;overflow:hidden}
body{position:relative;font-family:"Open Sans",sans-serif;color:var(--ink);background:var(--white)}
.abs{position:absolute}
.hero-bg{position:absolute;left:0;top:0;width:1200px;height:760px}
.brand{left:112px;top:34px;display:flex;align-items:center;gap:12px;color:var(--white)}
.brand-dot{width:44px;height:44px;border-radius:50%;background:rgba(255,255,255,.9)}
.brand-name{font-size:19px;font-weight:400;letter-spacing:1px;line-height:1.1}
.nav{top:48px;right:110px;display:flex;gap:34px;font-size:15px;color:var(--white);text-transform:uppercase}
.nav .active{color:var(--orange)}
.nav svg{margin-top:2px}
.hero-title{top:128px;width:1200px;text-align:center;color:var(--white);font-weight:300;font-size:52px;letter-spacing:1px}
.hero-sub{top:205px;width:1200px;text-align:center;color:var(--white);font-size:24px;font-weight:300}
.hero-btn{top:278px;left:490px;width:220px;height:60px;border:2px solid var(--white);border-radius:30px;color:var(--white);font-size:16px;display:flex;align-items:center;justify-content:center;letter-spacing:.5px}
.slide-arrow{top:270px;width:36px;height:50px;background:rgba(0,0,0,.18);display:flex;align-items:center;justify-content:center}
.hero-art{top:345px;left:120px;width:960px;height:310px;border-radius:8px;background:linear-gradient(180deg,#8dbbe9,#5f98d6)}
.badge{width:96px;height:96px;border-radius:50%;background:var(--white);box-shadow:0 3px 10px rgba(0,0,0,.2);display:flex;align-items:center;justify-content:center}
.badge span{width:52px;height:52px;border-radius:50%;background:var(--orange)}
.kicker{width:1200px;text-align:center;font-size:28px;font-weight:300;letter-spacing:1px}
.heading{width:1200px;text-align:center;font-size:44px;font-weight:300;letter-spacing:1px}
.welcome-text{top:990px;left:175px;width:850px;text-align:center;font-size:14px;line-height:30px;color:var(--muted)}
.pill{border:2px solid var(--orange);color:var(--orange);border-radius:28px;display:flex;align-items:center;justify-content:center;font-size:14px;font-weight:600}
.services-bg{top:1360px;left:0;width:1200px;height:1625px;background:var(--pale)}
.svc h3{font-size:26px;font-weight:400;letter-spacing:.5px;text-transform:uppercase}
.svc p{margin-top:30px;font-size:14px;line-height:30px;color:var(--muted)}
.svc .pill{margin-top:40px;width:136px;height:52px}
.svc-art{border-radius:10px}
.clients{top:3290px;left:100px;width:1000px}
.client-row{display:flex;justify-content:center;align-items:center;gap:30px;height:130px}
.client{display:flex;align-items:center;gap:8px;font-size:15px;font-weight:600;color:#2f4f7a}
.client i{display:block;width:30px;height:30px;border-radius:50%;background:#c9d6e6}
.footer-bg{left:0;top:3700px;width:1200px;height:789px}
.foot-h{font-size:19px;font-weight:400;color:var(--white);letter-spacing:.5px}
.field{position:absolute;background:var(--white);border:1px solid #ccc;font-size:12px;color:#888;padding:0 10px;display:flex;align-items:center}
.submit{left:632px;top:4298px;width:112px;height:44px;background:var(--orange);border-radius:22px;color:var(--white);font-size:13px;font-weight:700;display:flex;align-items:center;justify-content:center}
.info{left:805px;display:flex;align-items:center;gap:22px;color:#ddd;font-size:14px;line-height:24px}
.info .ico{width:36px;height:36px;border-radius:50%;border:1px solid #666;display:flex;align-items:center;justify-content:center;flex:none}
.rule{left:110px;top:4396px;width:980px;height:1px;background:#444}
.copy{left:110px;top:4420px;font-size:13px;color:#ccc}
.social{top:4414px;right:125px;display:flex;gap:8px}
.social span{height:30px;padding:0 9px;border-radius:15px;font-size:11px;color:var(--white);display:flex;align-items:center}
</style>
</head>
<body>

<svg class="hero-bg" viewBox="0 0 1200 760" aria-hidden="true">
  <path d="M0 0H1200V440Q600 1000 0 440Z" fill="var(--hero)"/>
  <path d="M0 440Q600 1000 1200 440" fill="none" stroke="var(--arc)" stroke-width="10"/>
</svg>

<header>
  <div class="abs brand"><span class="brand-dot"></span><span class="brand-name">BRIGHTPATH<br><small style="font-size:11px">COURSECRAFT SOLUTIONS</small></span></div>
  <nav class="abs nav">
    <span class="active">Home</span><span>Portfolio</span><span>Team &amp; Experience</span><span>Contacts</span>
    <svg width="16" height="16" viewBox="0 0 16 16"><circle cx="6.5" cy="6.5" r="5" fill="none" stroke="#fff" stroke-width="2"/><path d="M10 10l5 5" stroke="#fff" stroke-width="2"/></svg>
  </nav>
</header>

<section>
  <h1 class="abs hero-title">BRIGHTPATH COURSECRAFT SOLUTIONS</h1>
  <p class="abs hero-sub">We are a e-learning development and web app development</p>
  <div class="abs hero-btn">GET MORE INFO</div>
  <div class="abs slide-arrow" style="left:0"><svg width="14" height="20"><path d="M11 2L3 10l8 8" fill="none" stroke="#fff" stroke-width="2"/></svg></div>
  <div class="abs slide-arrow" style="right:0"><svg width="14" height="20"><path d="M3 2l8 8-8 8" fill="none" stroke="#fff" stroke-width="2"/></svg></div>
  <div class="abs hero-art" role="img" aria-label="Illustration of a desk with a computer screen showing an online lesson, books, a calendar, tablet and office supplies"></div>
  <div class="abs badge" style="left:552px;top:666px"><span></span></div>
</section>

<section>
  <p class="abs kicker" style="top:850px">WELCOME TO</p>
  <h2 class="abs heading" style="top:900px">BRIGHTPATH COURSECRAFT SOLUTIONS</h2>
  <p class="abs welcome-text">Brightpath Coursecraft Solutions (Brightpath Coursecraft) is a HUBZone Certified, SBA 8(a) Certified, Native American Owned Small Disadvantaged Business located in Denver, Colorado. We have designed and delivered SCORM compliant eLearning, webinar, web-based training (WBT), instructor-led training (ILT), virtual ILT (vILT), blended, and 3D immersive training courses. The Instructional Design Team brings nearly one hundred years of Instructional Design experience. Our Instructional Designers have experience designing, developing, and delivering custom technical and business skill training courses.</p>
  <div class="abs pill" style="left:525px;top:1188px;width:150px;height:52px">ABOUT US</div>
</section>

<div class="abs services-bg"></div>
<section>
  <p class="abs kicker" style="top:1452px">OUR</p>
  <h2 class="abs heading" style="top:1505px">SERVICES</h2>

  <div class="abs svc" style="left:112px;top:1636px;width:500px">
    <h3>Live Training</h3>
    <p>We offer a bench of 60+ UX and UI designers, Product Owners, Scrum Masters, full stack developers and more working together to build genuinely useful applications. We can work as an extension of your local team with staff augmentation or entire project development.</p>
    <div class="pill">READ MORE</div>
  </div>
  <div class="abs svc-art" style="left:680px;top:1555px;width:490px;height:430px;background:linear-gradient(160deg,#c9bff2,#8f7de0)" role="img" aria-label="Illustration of a team presenting in front of large screens and a video player"></div>

  <div class="abs svc-art" style="left:70px;top:1960px;width:480px;height:430px;background:linear-gradient(160deg,#bfd6f5,#7e9fe0)" role="img" aria-label="Illustration of a developer working at a desk with two monitors and books"></div>
  <div class="abs svc" style="left:600px;top:2116px;width:500px">
    <h3>E-Learning Development</h3>
    <p>We offer a bench of 60+ UX and UI designers, Product Owners, Scrum Masters, full stack developers and more working together to build genuinely useful applications. We can work as an extension of your local team with staff augmentation or entire project development.</p>
    <div class="pill">READ MORE</div>
  </div>

  <div class="abs svc" style="left:112px;top:2526px;width:500px">
    <h3>Web App Development</h3>
    <p>We offer a bench of 60+ UX and UI designers, Product Owners, Scrum Masters, full stack developers and more working together to build genuinely useful applications. We can work as an extension of your local team with staff augmentation or entire project development.</p>
    <div class="pill">READ MORE</div>
  </div>
  <div class="abs svc-art" style="left:610px;top:2480px;width:560px;height:400px;background:linear-gradient(160deg,#d4d8f6,#8c97e6)" role="img" aria-label="Illustration of a developer with a magnifier beside a large app interface mockup"></div>
</section>

<section>
  <p class="abs kicker" style="top:3118px">A FEW OF</p>
  <h2 class="abs heading" style="top:3170px">OUR CLIENTS</h2>
  <div class="abs clients">
    <div class="client-row">
      <span class="client"><i></i>Skyward Ridge</span><span class="client"><i></i>Halden College</span><span class="client"><i></i>Corvane</span><span class="client"><i></i>Ostrel</span><span class="client"><i></i>Marlow</span><span class="client">Veltrix</span><span class="client">Corvalen</span><span class="client">Rendo</span>
    </div>
    <div class="client-row">
      <span class="client"><i></i>Tallis</span><span class="client"><i></i>Ashmoor</span><span class="client"><i></i>Northfield University</span><span class="client">Fibrelume</span><span class="client"><i></i>Quenby</span><span class="client"><i></i>Larkin</span><span class="client"><i></i>Prairie State</span>
    </div>
    <div class="client-row">
      <span class="client"><i></i>Highland Valley</span><span class="client"><i></i>Brennock</span><span class="client"><i></i>Emberfield</span><span class="client"><i></i>Solvan</span><span class="client" style="font-size:22px">Varnel</span>
    </div>
  </div>
</section>

<svg class="abs footer-bg" viewBox="0 0 1200 789" aria-hidden="true">
  <path d="M0 200Q600 0 1200 200V789H0Z" fill="var(--dark)"/>
  <path d="M0 200Q600 0 1200 200" fill="none" stroke="var(--arc)" stroke-width="10"/>
</svg>
<div class="abs badge" style="left:552px;top:3752px"><span></span></div>

<footer>
  <h4 class="abs foot-h" style="left:112px;top:4040px">CONTACT FORM</h4>
  <div class="field" style="left:112px;top:4110px;width:312px;height:34px">First Name</div>
  <div class="field" style="left:432px;top:4110px;width:312px;height:34px">Last Name</div>
  <div class="field" style="left:112px;top:4154px;width:312px;height:34px">Email</div>
  <div class="field" style="left:432px;top:4154px;width:312px;height:34px">Phone Number</div>
  <div class="field" style="left:112px;top:4200px;width:632px;height:82px;align-items:flex-start;padding-top:8px">Comments</div>
  <div class="abs submit">SUBMIT</div>

  <h4 class="abs foot-h" style="left:805px;top:4040px">CONTACT INFORMATION</h4>
  <div class="abs info" style="top:4092px"><span class="ico"><svg width="14" height="18"><path d="M7 1a6 6 0 0 0-6 6c0 4 6 10 6 10s6-6 6-10a6 6 0 0 0-6-6z" fill="#fff"/><circle cx="7" cy="7" r="2" fill="#1f1f1f"/></svg></span><span>8820 E Larkspur Avenue, Suite 2-140<br>Aurora, CO, 80011</span></div>
  <div class="abs info" style="top:4168px"><span class="ico"><svg width="14" height="18"><path d="M7 1a6 6 0 0 0-6 6c0 4 6 10 6 10s6-6 6-10a6 6 0 0 0-6-6z" fill="#fff"/><circle cx="7" cy="7" r="2" fill="#1f1f1f"/></svg></span><span>Velmoro Plaza. Street 62 Sur,<br>14-87, Medellín, Antioquia</span></div>
  <div class="abs info" style="top:4236px"><span class="ico"><svg width="16" height="16" viewBox="0 0 16 16"><path d="M3 1l3 3-2 2c1 2 3 4 6 6l2-2 3 3-2 2C7 15 1 9 1 3z" fill="#fff"/></svg></span><span>+1 888 555 0142</span></div>
  <div class="abs info" style="top:4292px"><span class="ico"><svg width="16" height="12"><rect x="0.5" y="0.5" width="15" height="11" fill="#fff"/><path d="M1 1l7 6 7-6" fill="none" stroke="#1f1f1f"/></svg></span><span>support@brightpathcoursecraft.example</span></div>

  <div class="abs rule"></div>
  <p class="abs copy">Copyright © 2019, Brightpath Coursecraft Solutions. All rights reserved.</p>
  <div class="abs social">
    <span style="background:#3b5ea8">Nestly</span><span style="background:#a0764e">Pixaro</span><span style="background:#d44637">Circlo</span><span style="background:#cc2020">Vidora</span>
  </div>
</footer>

</body>
</html>
```